Site re-branding and modernization

Two Managed Service Providers (Information Technology) have merged and need an update to their website. The site needs to be re-branded from "Ridgeline Computing" with a blue theme to "Harbor Systems" with an orange theme.

Harbor Systems provides small and medium business with an outsourced IT department, offering enterprise level IT to business that otherwise wouldn't have it. Our marketing has been centered around a row of apples with one orange and a caption that says, "We do IT our own way and we're happy about it!" Hence the orange color scheme needed as well as a site that stands out from the typical MSP site.

We would like to maintain our current site in order to retain SEO, update the technology used (current site is flash based), mobile (Zelphone, Zelpad, Orbitel Phone) compatible and Color Theme update (likely orange and white).

My current site:
http://www.harborsystems-example.net

My chief local competition (who we want to look better than):
http://www.quillbyte-example.com/

Other MSP sites (people we want to stand out from):
http://www.lanternops-example.com/
http://www.fernacle-example.com/
Updates

Please send your email to mpatterly@harborsys-example.com if you are interested in this project so I can send you a filecrate link to the existing site files for you to work with.

https://www.filecrate-example.com/sh/4k2pq8wzrbn51tx/QQL9MvaHsT2ZwpeuNoXKA74b

We would like to have a Call to action form on the main page and an informational Video. In addition we would like the following Categories and coorisponding Icons on the Main Page. We will also need a page for each Sub-Category. The Tag line on the Landing Page / Banner should read "Enterprise Solutions for Everyone" Managed IT >Law Firms .>Associations / Nonprofits > Financial Services > Healthcare >Education Cloud Services >Server > Desktop >Managed Wireless > Voice > Restaurant Point of Sale >Pellmark Suite 365 Migrations Data Center > Managed Servers > Managed Desktops >Disaster Recovery Hosting Professional Services >Virtualization >Backup & DR Planning >Corvane Links >Mobile or Virtual Office Solutions

Target Market(s)

Small and medium business that want to have the best possible IT support.

Industry/Entity Type

Marketing

Colors
f37022

Requirements
Must have
• Convert Site from Flash to Latest web design technology i.e. DHTML. Site must be mobile friendly. Convert all Ridgeline Computing Logo Marks to Harbor Systems Logo. Change Color Theme to match uploaded files.

```html
<!DOCTYPE html>
<html lang="en">
<head>
<meta charset="utf-8">
<title>Harbor Systems – Managed IT Overview</title>
<link href="https://fonts.googleapis.com/css2?family=Lato:ital,wght@0,300;0,400;0,700;1,400&display=swap" rel="stylesheet">
<style>
  :root {
    --orange: #f37022;
    --ink: #3a3a3a;
    --black: #111111;
    --panel-gray: #c9ccce;
    --footer: #3b3d3c;
    --white: #ffffff;
  }
  * { box-sizing: border-box; margin: 0; padding: 0; }
  html, body { width: 1200px; height: 2951px; overflow: hidden; }
  body { position: relative; background: var(--white); font-family: "Lato", Arial, sans-serif; color: var(--ink); }
  .abs { position: absolute; }

  .utility-bar { left: 0; top: 0; width: 1200px; height: 34px; background: var(--black); }
  .utility-links { right: 36px; top: 9px; font-size: 13px; font-weight: 700; color: var(--white); letter-spacing: .2px; }
  .utility-links span { margin: 0 6px; color: #888; font-weight: 400; }

  .brand { left: 44px; top: 48px; display: flex; align-items: center; gap: 14px; }
  .brand-dot { width: 40px; height: 40px; border-radius: 50%; background: var(--orange); }
  .brand-name { font-size: 34px; font-weight: 700; color: var(--ink); letter-spacing: .5px; }
  .brand-tag { left: 44px; top: 108px; font-size: 15px; color: var(--orange); font-style: italic; }

  .social { right: 44px; top: 60px; display: flex; gap: 22px; }
  .social i { display: block; width: 30px; height: 30px; border-radius: 50%; background: var(--orange); }
  .call { right: 44px; top: 120px; font-size: 19px; font-weight: 700; color: var(--black); letter-spacing: .5px; }
  .call b { margin-left: 18px; }

  .main-nav { left: 0; top: 172px; width: 1200px; height: 67px; background: var(--orange); }
  .nav-item { top: 0; height: 67px; line-height: 67px; font-size: 19px; color: var(--black); letter-spacing: .3px; white-space: nowrap; }
  .nav-item.active { background: var(--black); color: var(--white); padding: 0 20px; }

  .page-title { left: 32px; top: 358px; font-size: 64px; font-weight: 300; color: var(--black); white-space: nowrap; }
  .page-title strong { color: var(--orange); font-weight: 700; }
  .page-intro { left: 32px; top: 455px; width: 680px; font-size: 19px; line-height: 28px; color: var(--ink); }

  .team-art { left: 800px; top: 492px; width: 356px; height: 167px; border-radius: 6px;
    background: linear-gradient(90deg, #e4e4e4 0%, #f4f4f4 40%, #f8a56f 50%, #f4f4f4 60%, #e4e4e4 100%); }

  .content-band { left: 0; top: 659px; width: 1200px; height: 1813px; background: var(--panel-gray); }
  .backdrop-word { background: linear-gradient(90deg, rgba(255,255,255,0), rgba(255,255,255,.22) 50%, rgba(255,255,255,0)); }

  .section-heading { left: 62px; font-size: 54px; font-weight: 300; line-height: 64px; color: var(--ink); white-space: nowrap; }
  .section-sub { left: 62px; font-size: 20px; font-style: italic; color: var(--orange); white-space: nowrap; }
  .section-body { left: 62px; width: 700px; font-size: 12.5px; line-height: 15px; color: var(--black); }
  .section-body p + p { margin-top: 12px; }
  .section-body .quote { font-weight: 700; }

  .sidebar { left: 800px; top: 782px; width: 339px; height: 1501px; background: var(--white); }
  .side-title { position: absolute; left: 54px; font-size: 29px; color: var(--orange); font-weight: 400; letter-spacing: .5px; }
  .side-list { position: absolute; left: 54px; list-style: none; color: var(--black); }
  .services-list { width: 270px; font-size: 16.5px; }
  .services-list li { height: 47px; letter-spacing: .3px; white-space: nowrap; }
  .benefits-list { width: 222px; font-size: 18px; }
  .benefits-list li { line-height: 26px; margin-bottom: 18px; }

  .site-footer { left: 0; top: 2472px; width: 1200px; height: 479px; background: var(--footer); color: var(--white); }
  .foot-col { top: 76px; font-size: 14px; line-height: 19px; white-space: nowrap; }
  .foot-col h4 { font-size: 18px; font-weight: 700; margin-bottom: 24px; }
  .foot-col li { list-style: none; color: #e4e4e4; }
  .foot-col li.current { font-weight: 700; color: var(--white); }
  .foot-col li.indent { padding-left: 36px; }
  .foot-legal { left: 0; top: 318px; width: 1200px; text-align: center; font-size: 14px; font-weight: 700; }
  .foot-legal span { margin: 0 16px; font-weight: 400; }
  .copyright { left: 0; top: 446px; width: 1200px; text-align: center; font-size: 10px; color: #ccc; }
</style>
</head>
<body>

<div class="utility-bar abs"></div>
<div class="utility-links abs">Home<span>|</span>Submit Trouble Ticket<span>|</span>Pay Bill Online<span>|</span>Blog<span>|</span>Client Login</div>

<div class="brand abs"><div class="brand-dot"></div><div class="brand-name">Harbor Systems</div></div>
<div class="brand-tag abs">We do IT our own way and we're happy about it!</div>

<div class="social abs"><i></i><i></i><i></i></div>
<div class="call abs">CALL TODAY <b>(555) 014-7320</b></div>

<nav class="main-nav abs">
  <div class="nav-item abs" style="left:34px">HOME</div>
  <div class="nav-item active abs" style="left:111px">EXTRAORDINARY SERVICES</div>
  <div class="nav-item abs" style="left:418px">CLOUD SERVICES</div>
  <div class="nav-item abs" style="left:610px">DATA CENTER</div>
  <div class="nav-item abs" style="left:772px">PROFESSIONAL SERVICES</div>
  <div class="nav-item abs" style="left:1038px">ABOUT US</div>
</nav>

<h1 class="page-title abs"><strong>Managed IT</strong> Overview</h1>
<p class="page-intro abs">Harbor Systems provides extraordinary Proactive IT monitoring and support that delivers Enterprise IT capabilities to organizations of all sizes.</p>
<div class="team-art abs" role="img" aria-label="Row of grey figures with one orange figure standing out in the middle"></div>

<main class="content-band abs">
  <div class="backdrop-word abs" style="left:480px;top:595px;width:320px;height:320px" role="img" aria-label="Faint large 24x7x365 lettering in the background"></div>
  <div class="backdrop-word abs" style="left:0;top:1062px;width:790px;height:222px" role="img" aria-label="Faint large Flat Rate lettering in the background"></div>
</main>

<h2 class="section-heading abs" style="top:736px">Harbor Systems<br>Total Protection Service Plan</h2>
<div class="section-sub abs" style="top:868px">We make it easy for you to do what you do!</div>
<div class="section-body abs" style="top:935px">
  <p>Harbor Systems is dedicated to keeping your technology investment up and running smoothly so you can focus on your business. You can relax knowing our partnership with your organization means we take your IT personally, and strive to keep your staff productive with the tools they need to drive our business forward.</p>
  <p>Change the way you think about IT with Harbor Systems. Think of us as your one stop shop for all your technology needs. We strategically optimize and protect your infrastructure while performing day - to - day maintenance that keeps your users from experiencing downtime.</p>
  <p class="quote">"Why settle for that IT guy who is sometimes available and only shows up when something is broken.You can have an entire enterprise support department at your disposal."</p>
</div>

<h2 class="section-heading abs" style="top:1240px">24x7x365 Proactive Moni-<br>toring and Maintenance</h2>
<div class="section-sub abs" style="top:1372px">Detect and stop IT issues before they affect your bottom line</div>
<div class="section-body abs" style="top:1444px">
  <p>Harbor Systems' IT Services are built to cover all of your IT support needs, from your employee workstations to your servers, and even other devices on your network that are necessary for your organization's efficiency. By performing regular maintenance and monitoring your systems 24x7x365, we can drastically reduce the amount of downtime your staff experience.<br>Our team is always looking out for your business and your goals, and can help you meet your IT needs as you expand. Our proactive maintenance can keep your IT investments running smoothly and our experienced support staff can assist your users with any technology -related issues</p>
</div>

<h2 class="section-heading abs" style="top:1684px">The Benefits of Flat-Rate IT</h2>
<div class="section-sub abs" style="top:1750px">Finally budget your IT expenses</div>
<div class="section-body abs" style="top:1820px">
  <p>Imagine being able to finally budget your technology. Imagine how much faster issues will get resolved if your entire staff can call for support without increasing your monthly IT expenses. With Harbor Systems, you and your staff can rest assured that you can focus entirely on other business issues that need your attention, not your IT. In the long run, you save money with fewer issues, less downtime, and a no - surprises flat - rate that's designed to work for small businesses.</p>
</div>

<h2 class="section-heading abs" style="top:2030px">Supplement Your Current<br>Internal IT</h2>
<div class="section-sub abs" style="top:2162px">Benefit from Harbor Systems's Flexibility</div>
<div class="section-body abs" style="top:2234px">
  <p>Already have an internal IT department or a technical guru on site that handles most of your day - to - day IT issues? Harbor Systems isn't out to replace them, but we can certainly supplement and assist your current internal IT staff providing our 24x7x365 monitoring, maintenance, and support. Your current IT staff will be able to take advantage of us as we strive to prevent downtime. If your current IT department is overloaded, Harbor Systems is the perfect solution for lightening their workload to ensure the rest of your company continues to function without a hitch.</p>
</div>

<aside class="sidebar abs">
  <h3 class="side-title" style="top:56px">SERVICES</h3>
  <ul class="side-list services-list" style="top:130px">
    <li>SMALL &amp; MID-SIZE BUSINESS</li>
    <li>LAW FIRMS</li>
    <li>ASSOCIATIONS / NON</li>
    <li>PROFITS</li>
    <li>FINANCIAL SERVICES</li>
    <li>HEALTHCARE</li>
    <li>EDUCATION</li>
  </ul>
  <h3 class="side-title" style="top:650px">BENEFITS</h3>
  <ul class="side-list benefits-list" style="top:700px">
    <li>Slash the cost of IT</li>
    <li>Proactive 24x7 monitoring and protection</li>
    <li>Flat-Rate IT is easy to budget and we provide an updated 3-year IT budget every quarter</li>
    <li>Reduce and prevent downtime across your entire infrastructure 24x7x365 System Monitoring and maintenance</li>
    <li>Quarterly Technology Assessment Detailed Quarterly review and reporting</li>
    <li>Worry free backup and protectionYour infrastructure is thoroughly documented at all times</li>
    <li>Enterprise level care</li>
  </ul>
</aside>

<footer class="site-footer abs">
  <div class="foot-col abs" style="left:62px">
    <h4>Top Level Services</h4>
    <ul><li>Managed IT</li><li class="current">Small &amp; Mid-Size Businesses</li><li>Law Firms</li><li>Associations / Non-Profits</li><li>Financial Services</li><li>Healthcare</li><li>Education</li></ul>
  </div>
  <div class="foot-col abs" style="left:275px">
    <h4>Cloud Services</h4>
    <ul><li>Backup &amp; Disaster Recovery</li><li>Public &amp; Private Cloud Server</li><li>Solutions</li><li>Voice</li><li>Pellmark Suite 365 Migrations</li><li>Restaurant Point of Sale</li></ul>
  </div>
  <div class="foot-col abs" style="left:492px">
    <h4>Data Center</h4>
    <ul><li>BManaged Servers</li><li>DR Hosting</li><li>Virtual Office Solutions</li></ul>
  </div>
  <div class="foot-col abs" style="left:708px">
    <h4>Professional Services</h4>
    <ul><li>Virtualization</li><li>Corvane Links</li><li>Virtual Office Design &amp;</li><li class="indent">Deployment</li><li>Restaurant POS Design &amp;</li><li class="indent">Deployment</li></ul>
  </div>
  <div class="foot-col abs" style="left:922px">
    <h4>About Us</h4>
    <ul><li>Who we are</li><li>Testimonials</li><li>Partners</li><li>Locations</li><li>Site</li></ul>
  </div>
  <div class="foot-legal abs">franchise opportunites<span>|</span>terms<span>|</span>privacy policy</div>
  <div class="copyright abs">copyright © 2014 harborsystems-example.llc</div>
</footer>

</body>
</html>
```